Updated DJ business Card showing other businesses

DJ Talbo offers professional mobile dj services including DJ. MC. Karaoke.
Hush Party (will attach logo)
I also offer a 360 Photo Booth.

Contact info:
(405) 555-0147
mark.fenstell@pelimail.com
Social Media @DJTalboOKC

```html
<!DOCTYPE html>
<html lang="en">
<head>
<meta charset="utf-8">
<title>DJ Talbo Business Card</title>
<link href="https://fonts.googleapis.com/css2?family=Lato:wght@400;700;900&family=Roboto+Condensed:wght@500;700&display=swap" rel="stylesheet">
<style>
  :root {
    --backdrop: #2b2b2b;
    --card-black: #0f0f10;
    --card-white: #ffffff;
    --ink: #111111;
    --accent-red: #d01f48;
    --muted-mark: #1c1c1e;
    --paper-text: #ffffff;
  }
  * { margin: 0; padding: 0; box-sizing: border-box; }
  html, body { width: 1200px; height: 900px; overflow: hidden; }
  body {
    background: var(--backdrop);
    font-family: "Lato", sans-serif;
    position: relative;
  }
  .card {
    position: absolute;
    left: 250px;
    width: 700px;
    height: 400px;
    border-radius: 22px;
    overflow: hidden;
  }
  /* Back side */
  .card-back { top: 40px; background: var(--card-black); color: var(--paper-text); }
  .back-decoration { position: absolute; left: 0; top: 0; width: 300px; height: 400px; }
  .brand-name {
    position: absolute;
    left: 160px; top: 68px;
    width: 520px;
    font-family: "Lato", sans-serif;
    font-weight: 900;
    font-size: 92px;
    letter-spacing: 1px;
    line-height: 1;
    white-space: nowrap;
    color: var(--paper-text);
    text-align: center;
  }
  .services {
    position: absolute;
    left: 90px; top: 196px;
    width: 590px;
    font-family: "Roboto Condensed", sans-serif;
    text-transform: uppercase;
    text-align: center;
    white-space: nowrap;
  }
  .services-intro { font-size: 17px; font-weight: 700; letter-spacing: 0.5px; }
  .services-list {
    margin-top: 8px;
    display: flex; align-items: center; justify-content: center; gap: 12px;
    font-size: 44px; font-weight: 700; line-height: 1;
  }
  .services-list .divider { font-weight: 500; font-size: 40px; }
  .partner {
    display: flex; align-items: center; gap: 7px;
    font-family: "Roboto Condensed", sans-serif;
    font-size: 20px; font-weight: 700;
    white-space: nowrap;
  }
  .partner-dot { width: 20px; height: 20px; border-radius: 50%; border: 2px solid var(--paper-text); flex: none; }
  .services-extra { margin-top: 10px; font-size: 15px; font-weight: 700; letter-spacing: 0.4px; }

  /* Front side */
  .card-front { top: 460px; background: var(--card-white); color: var(--ink); }
  .mascot-area { position: absolute; right: 0; top: 0; width: 400px; height: 400px; }
  .identity { position: absolute; left: 48px; top: 48px; }
  .person-name { font-weight: 900; font-size: 54px; line-height: 1; letter-spacing: 0.5px; white-space: nowrap; }
  .person-role { margin-top: 6px; color: var(--accent-red); font-size: 22px; line-height: 1.2; }
  .contact-list { list-style: none; margin-top: 18px; }
  .contact-list li { display: flex; align-items: center; gap: 12px; font-size: 19px; line-height: 1.55; white-space: nowrap; }
  .contact-list .phone { font-weight: 700; font-size: 26px; }
  .contact-icon { width: 18px; height: 18px; flex: none; }
  .social-handle { margin-top: 20px; font-weight: 700; font-size: 21px; }
</style>
</head>
<body>

<section class="card card-back">
  <svg class="back-decoration" viewBox="0 0 300 400" role="img" aria-label="Faint oversized rhino mascot decoration">
    <path d="M0 0 H210 C260 90 270 260 230 400 H0 Z" fill="var(--muted-mark)"/>
  </svg>
  <div class="brand-name">DJ TALBO</div>
  <div class="services">
    <p class="services-intro">DJ Talbo offers professional mobile DJ services</p>
    <div class="services-list">
      <span>DJ</span><span class="divider">|</span>
      <span>MC</span><span class="divider">|</span>
      <span>Karaoke</span><span class="divider">|</span>
      <span class="partner"><span class="partner-dot"></span>Hush Party</span>
    </div>
    <p class="services-extra">I also offer a 360 photo booth.</p>
  </div>
</section>

<section class="card card-front">
  <svg class="mascot-area" viewBox="0 0 400 400" role="img" aria-label="Large rhino mascot illustration">
    <path d="M60 400 C90 330 110 260 130 200 C150 150 180 110 230 90 L270 0 H400 V400 Z" fill="var(--ink)"/>
  </svg>
  <div class="identity">
    <h1 class="person-name">DJ TALBO</h1>
    <p class="person-role">Founder/Owner/ DJ<br>Trumpet Player/Vocalist</p>
    <ul class="contact-list">
      <li class="phone">
        <svg class="contact-icon" viewBox="0 0 24 24"><path d="M6.6 10.8a15 15 0 0 0 6.6 6.6l2.2-2.2a1 1 0 0 1 1-.25 11.4 11.4 0 0 0 3.6.57 1 1 0 0 1 1 1V20a1 1 0 0 1-1 1A17 17 0 0 1 3 4a1 1 0 0 1 1-1h3.5a1 1 0 0 1 1 1c0 1.25.2 2.45.57 3.6a1 1 0 0 1-.25 1z" fill="var(--accent-red)"/></svg>
        (405) 555-0147
      </li>
      <li>
        <svg class="contact-icon" viewBox="0 0 24 24"><rect x="2" y="5" width="20" height="14" rx="1.5" fill="var(--accent-red)"/><path d="M3 6l9 7 9-7" stroke="#fff" stroke-width="1.6" fill="none"/></svg>
        mark.fenstell@pelimail.com
      </li>
      <li>
        <svg class="contact-icon" viewBox="0 0 24 24"><circle cx="12" cy="12" r="9" fill="none" stroke="var(--accent-red)" stroke-width="2"/><path d="M3 12h18M12 3c3 3 3 15 0 18M12 3c-3 3-3 15 0 18" stroke="var(--accent-red)" stroke-width="1.6" fill="none"/></svg>
        www.talbobeats.com
      </li>
    </ul>
    <p class="social-handle">@DJTalboOKC</p>
  </div>
</section>

</body>
</html>
```